New Business Card Design Project

Need a design that will create an impact / strong impression towards our clients for our business. We are in the lighting business and we do lighting retrofits for large commercial to industrial clientele.

Target Market(s)

Lighting Industry

Industry/Entity Type

Business

Font styles to use
Other font styles liked:
• we would like to use the font on our logo, not sure what it is though..

Requirements
Must have
• Our logo.
Nice to have
• We are open to suggestions that have to do with lighting.

```html
<!DOCTYPE html>
<html lang="en">
<head>
<meta charset="utf-8">
<title>Brightline Retrofit Co. – Business Card</title>
<link href="https://fonts.googleapis.com/css2?family=Roboto+Condensed:wght@400;700&display=swap" rel="stylesheet">
<style>
  :root {
    --backdrop: #e6e6e3;
    --card-white: #ffffff;
    --green-dark: #114a1a;
    --green-mid: #1d6e2b;
    --green-light: #3ea64c;
    --text-grey: #5a5a5a;
    --icon-grey: #3c3c3c;
  }
  * { margin: 0; padding: 0; box-sizing: border-box; }
  html, body { width: 1200px; height: 911px; overflow: hidden; }
  body {
    background: var(--backdrop);
    font-family: "Roboto Condensed", "Arial Narrow", sans-serif;
    position: relative;
  }
  .card {
    position: absolute;
    top: 307px;
    width: 520px;
    height: 297px;
    border-radius: 18px;
    box-shadow: 0 6px 18px rgba(0,0,0,.18);
    overflow: hidden;
  }
  .card-front { left: 50px; background: var(--card-white); }
  .card-back { left: 630px; background: var(--green-dark); }

  /* Front */
  .brand-front {
    position: absolute;
    left: 40px;
    bottom: 52px;
    display: flex;
    align-items: center;
    gap: 10px;
    color: var(--green-mid);
    font-weight: 700;
    font-size: 30px;
    letter-spacing: .5px;
  }
  .brand-mark { width: 16px; height: 16px; background: var(--green-mid); }
  .contact {
    position: absolute;
    left: 300px;
    top: 38px;
    color: var(--text-grey);
  }
  .contact-name {
    font-weight: 700;
    font-size: 21px;
    color: var(--green-mid);
    letter-spacing: .3px;
  }
  .contact-title {
    font-size: 14px;
    color: var(--green-light);
    margin-top: 1px;
    margin-bottom: 12px;
  }
  .contact-address { font-size: 13px; line-height: 16px; margin-bottom: 8px; }
  .contact-list { list-style: none; font-size: 13px; line-height: 18px; }
  .contact-list li { display: flex; align-items: center; gap: 7px; }
  .contact-list svg { width: 11px; height: 11px; fill: var(--icon-grey); flex: none; }

  /* Back */
  .brand-back {
    position: absolute;
    left: 0; right: 0;
    top: 108px;
    display: flex;
    justify-content: center;
    align-items: center;
    gap: 12px;
    color: var(--card-white);
    font-weight: 700;
    font-size: 40px;
    letter-spacing: .5px;
  }
  .brand-back .brand-mark { width: 20px; height: 20px; background: var(--card-white); }
  .back-web {
    position: absolute;
    left: 0; right: 0;
    bottom: 34px;
    text-align: center;
    color: var(--card-white);
    font-size: 13px;
    letter-spacing: 3px;
  }
</style>
</head>
<body>

<section class="card card-front">
  <div class="brand-front"><span class="brand-mark"></span>Brightline Retrofit</div>

  <div class="contact">
    <div class="contact-name">DANIEL REYES</div>
    <div class="contact-title">CEO/FOUNDER</div>
    <div class="contact-address">2140 Cedar Ridge Road<br>Juneau, Alaska 99801</div>
    <ul class="contact-list">
      <li>
        <svg viewBox="0 0 12 12"><path d="M2.5 1 L4.5 1 L5.3 3.4 L4 4.4 Q5 6.8 7.6 8 L8.6 6.7 L11 7.5 L11 9.5 Q11 11 9.4 11 Q1 10 1 2.6 Q1 1 2.5 1 Z"/></svg>
        907 555 0142
      </li>
      <li>
        <svg viewBox="0 0 12 12"><path d="M3 0.5 H9 V11.5 H3 Z M4 2 V9 H8 V2 Z"/></svg>
        907 555 0187
      </li>
      <li>
        <svg viewBox="0 0 12 12"><path d="M1 4 H11 V10.5 H1 Z M3 1 H9 V3.5 H3 Z"/></svg>
        907 555 0163
      </li>
      <li>
        <svg viewBox="0 0 12 12"><path d="M1 2.5 H11 V9.5 H1 Z M1.8 3.3 L6 6.5 L10.2 3.3 Z" fill-rule="evenodd"/></svg>
        daniel@brightlineretrofit.com
      </li>
      <li>
        <svg viewBox="0 0 12 12"><circle cx="6" cy="6" r="5"/></svg>
        www.brightlineretrofit.com
      </li>
    </ul>
  </div>
</section>

<section class="card card-back">
  <div class="brand-back"><span class="brand-mark"></span>Brightline Retrofit</div>
  <div class="back-web">www.brightlineretrofit.com</div>
</section>

</body>
</html>
```